New business card/stationary for a consulting company

I am looking for a clean and very professional looking business card for my consulting company as well as corresponding stationary. I am uploading our logo. I like simple and powerful for the feel. No graphics but I am open on everything else. Below is my contact information but would like the final to be in a version I can add my employees information into and print. Thank you.

Daniel Whitcombe
dan@ferncliffadvisory.com
2870 North 9th Avenue, Summit Floor, Elm Ridge, Illinois 60531
www.ferncliffadvisory.com

Industry/Entity Type

Consulting

Contact Information for Business Card

Daniel Whitcombe
dan@ferncliffadvisory.com
www.ferncliffadvisory.com

Font styles to use
Serif
Sans Serif

Requirements
Must have
• Our logo and the business card details.
Nice to have
• our website www.ferncliffadvisory.com

```html
<!DOCTYPE html>
<html lang="en">
<head>
<meta charset="utf-8">
<title>Ferncliff Advisory – Business Card</title>
<link href="https://fonts.googleapis.com/css2?family=Open+Sans:wght@400;700&display=swap" rel="stylesheet">
<style>
  :root {
    --backdrop: #8a8a8a;
    --card: #ffffff;
    --card-edge: #e4e4e4;
    --navy: #1b1a6b;
    --grey-text: #6a6a6a;
  }
  * { margin: 0; padding: 0; box-sizing: border-box; }
  html, body {
    width: 1200px;
    height: 904px;
    overflow: hidden;
    background: var(--backdrop);
    font-family: "Open Sans", Arial, sans-serif;
  }
  .stage {
    width: 1200px;
    height: 904px;
    display: flex;
    flex-direction: column;
    align-items: center;
    justify-content: center;
    gap: 40px;
  }
  .card {
    width: 640px;
    height: 366px;
    background: var(--card);
    border: 1px solid var(--card-edge);
    box-shadow: 0 8px 24px rgba(0, 0, 0, 0.25);
    display: flex;
    flex-direction: column;
    align-items: center;
    justify-content: center;
    text-align: center;
  }
  .card-contact .holder-name {
    color: var(--navy);
    font-weight: 700;
    font-size: 17px;
    margin-bottom: 6px;
  }
  .card-contact .contact-line {
    color: var(--grey-text);
    font-size: 13px;
    line-height: 1.45;
  }
  .card-brand .brand {
    display: flex;
    flex-direction: column;
    align-items: center;
    gap: 14px;
  }
  .card-brand .brand-square {
    width: 40px;
    height: 40px;
    background: var(--navy);
  }
  .card-brand .brand-name {
    color: var(--navy);
    font-weight: 400;
    font-size: 27px;
    letter-spacing: 1px;
    text-transform: uppercase;
  }
</style>
</head>
<body>
  <main class="stage">
    <section class="card card-contact">
      <p class="holder-name">Daniel Whitcombe</p>
      <p class="contact-line">2870 North 9th Avenue, Summit Floor, Elm Ridge, Illinois 60531</p>
      <p class="contact-line">dan@ferncliffadvisory.com | www.ferncliffadvisory.com</p>
    </section>
    <section class="card card-brand">
      <div class="brand">
        <span class="brand-square"></span>
        <p class="brand-name">Ferncliff Advisory</p>
      </div>
    </section>
  </main>
</body>
</html>
```